Copper Field Agency Website - Wordpress Web UPDATED BRIEF

FINAL LOGO UPLOADED - please look to this as reference for how we would like the site to look and feel.

We are a digital marketing agency - looking to have a new website built. We are looking for a simple one page feel of site that will allow us to grow it later. (Feel free to take some liberties with that if your imagination veers off) Must be very, playful, bold, sleek and easily integrate video. Wordpress only.

Overview:

Copper Field is a creative constellation. We are built on what's great about the shared economy. With access to thousands of content creators, designers, technicians, writers, strategists and other creatives around the world, we are built differently than a traditional “brick and mortar” Marketing Agency. We provide the traditional services our clients have come to expect, without the “5X factor” of covering the overhead common in the old agency model. We believe even better work can be created in collaboration with our clients and by passing those savings back to them for their use. Our clients pay for our art, our work and our passion –not our furniture.

"Copper Field, Let's Build Together"

Target Market(s)

companies looking for creative agency help, video production, creative consulting and coaching

Industry/Entity Type

Digital Marketing

Coding

Coded - Design and coding required

Number of Pages Required

1 page

Font styles to use
Sans Serif

Colors
3277b5
33a6d7
ec1f27

Requirements
Must have
• Wordpress design is a must. Looking for a one sheet homepage - with sections that are all on the main front page. We will have videos to embed, and should be able to have client logos and easy access to show a variety of our creative work.
• Please look to the logo for how we would like the site to feel.
• Please think "icon process flow" instead of blocks of text (which we used to have). Use the text to explain what the process flow should represent - don't actually copy paste the text but show it visually in icons.
Nice to have
• innovation around how we show video content. solid colors complementary to our palette and aesthetic.
Should not have
• Standard HTML coding

```html
<!DOCTYPE html>
<html lang="en">
<head>
<meta charset="utf-8">
<title>Copper Field Agency – Homepage Concepts</title>
<link rel="stylesheet" href="https://fonts.googleapis.com/css2?family=Roboto+Condensed:wght@700&family=Roboto:wght@400;500;700&display=swap">
<style>
:root{
  --blue:#2a62aa;
  --blue-deep:#1d4f91;
  --sky:#33a6d7;
  --red:#ec1f27;
  --ink:#2d2d2d;
  --muted:#6a6a6a;
  --navy:#10233f;
  --board:#6e6e6e;
  --soft:#f2f3f7;
  --line:#d9dde6;
}
*{box-sizing:border-box;margin:0;padding:0}
html,body{width:1200px;height:2495px;overflow:hidden}
body{background:var(--board);font-family:"Roboto",Arial,sans-serif;color:var(--ink);position:relative}
.page{position:absolute;top:56px;width:515px;height:2373px;background:#fff;overflow:hidden}
.page--a{left:58px}
.page--b{left:630px}
.abs{position:absolute}
.h{font-family:"Roboto Condensed","Arial Narrow",sans-serif;font-weight:700;text-transform:uppercase;color:var(--blue)}
.btn{position:absolute;background:var(--red);color:#fff;font-size:6px;font-weight:700;text-transform:uppercase;border-radius:10px;padding:5px 11px;letter-spacing:.2px;box-shadow:0 2px 4px rgba(236,31,39,.3)}
.body-txt{font-size:5.6px;line-height:2.2;color:var(--muted)}

/* header */
.phone{left:68px;top:9px;display:flex;align-items:center;gap:4px;color:var(--red);font-size:9.5px;font-weight:700}
.phone svg{width:13px;height:13px}
.social{left:378px;top:8px;display:flex;gap:5px}
.social span{width:14px;height:14px;border:1.2px solid var(--blue);border-radius:50%;position:relative}
.social span::after{content:"";position:absolute;left:4px;top:4px;width:4px;height:4px;border-radius:50%;background:var(--blue)}
.nav{right:66px;top:31px;display:flex;gap:8px;font-size:5.4px;color:var(--ink)}

/* hero */
.hero-shape{left:0;top:70px}
.mascot{left:72px;top:54px;width:168px;height:168px;border-radius:50%;background:radial-gradient(circle at 45% 35%,#5a8fd6,#1d4f91 60%,#0f2440);border:5px solid var(--navy)}
.wordmark{left:56px;top:228px;width:200px;text-align:center;font-size:28px;line-height:1;white-space:nowrap;color:var(--navy);letter-spacing:.5px}
.hero-title{left:260px;top:120px;color:#fff;font-size:18px;line-height:1.35}
.hero-text{left:260px;top:168px;color:#fff;font-size:7.6px;line-height:1.75;font-weight:500}
.hero-btn{left:260px;top:203px}
.slider-dot{left:28px;width:16px;height:16px;border:1px solid var(--line);border-radius:50%;font-size:7px;color:#999;text-align:center;line-height:14px}

/* about */
.about-shape{left:0;top:298px}
.laptop{left:70px;top:340px;width:170px;height:102px;background:linear-gradient(135deg,#f4f6fa,#dfe6f1);border:5px solid #1c1c1c;border-radius:3px}
.laptop-base{left:52px;top:442px;width:205px;height:5px;background:#b9bcc2;border-radius:0 0 6px 6px}
.about-title{left:264px;top:348px;font-size:15px}
.about-text{left:264px;top:371px;width:205px}
.about-btn{left:264px;top:445px}

/* services */
.svc-title{left:0;width:515px;top:520px;text-align:center;font-size:15px}
.svc-text{left:100px;width:315px;top:544px;text-align:center}
.svc-links{left:0;top:580px}
.svc{width:92px;height:92px;border-radius:50%;border:1px dashed #8aa6d2;text-align:center;padding-top:50px;background:#fff;box-shadow:0 0 0 3px #fff,0 0 0 4px #e6ecf5}
.svc b{display:block;font-size:6px;text-transform:uppercase;color:var(--ink)}
.svc i{display:block;font-style:normal;font-size:5px;line-height:1.5;color:var(--muted);width:62px;margin:2px auto 0}
.svc--on{background:var(--blue);border:0}
.svc--on b,.svc--on i{color:#fff}
.svc-fig{position:absolute;left:34px;top:10px;width:24px;height:36px;border-radius:10px;background:linear-gradient(#3b3f4a,#1e2a44)}
.svc--on .svc-fig{background:linear-gradient(#dfe6f1,#9bb1d6)}
.mascot-sm{left:200px;top:668px;width:118px;height:118px;border-radius:50%;background:radial-gradient(circle at 45% 35%,#5a8fd6,#1d4f91 60%,#0f2440);border:4px solid var(--navy)}
.wordmark-sm{left:178px;top:792px;width:160px;text-align:center;font-size:20px;line-height:1;white-space:nowrap;color:var(--navy)}

/* videos */
.video-band{left:0;top:860px}
.video-title{left:0;width:515px;top:900px;text-align:center;font-size:15px;color:#fff}
.video{left:86px;top:931px;width:343px;height:189px;background:linear-gradient(135deg,#8a7b6c,#c9bca9 45%,#5d5850)}
.play{left:159px;top:83px;width:24px;height:24px;border-radius:50%;background:#fff}
.play::after{content:"";position:absolute;left:9px;top:6px;border-left:9px solid var(--red);border-top:6px solid transparent;border-bottom:6px solid transparent}
.arrow{color:#fff;font-size:18px;top:1010px;font-weight:300}

/* work */
.work-title{left:0;width:515px;top:1197px;text-align:center;font-size:15px}
.work{width:121px;height:100px;background:linear-gradient(135deg,#4a6b94,#a9bdd6)}
.work:nth-child(2n){background:linear-gradient(135deg,#2e4e7a,#8fa7c8)}
.work:nth-child(3n){background:linear-gradient(135deg,#6c7480,#c4cbd6)}
.work span{position:absolute;left:0;bottom:10px;background:var(--blue);color:#fff;font-size:5.4px;font-weight:500;padding:3px 4px;text-transform:uppercase}
.work-btn{left:226px;top:1472px}

/* testimonials */
.testi-bg{left:0;top:1480px}
.testi-title{left:0;width:515px;top:1552px;text-align:center;font-size:15px}
.card{width:118px;height:65px;background:#fff;border-radius:4px;box-shadow:0 2px 6px rgba(0,0,0,.12);padding:8px}
.card .who{display:flex;gap:6px;align-items:center;font-size:4.8px;line-height:1.3;color:var(--ink)}
.card .who i{width:14px;height:14px;border-radius:50%;background:#d3d7de;flex:none}
.card p{font-size:4.3px;line-height:1.8;color:#888;font-style:italic;margin-top:6px}
.t-arrow{top:1606px;color:var(--blue);font-size:11px;font-weight:700}

/* process */
.step{left:16px;width:173px;background:#fff;box-shadow:0 2px 8px rgba(0,0,0,.1);padding:9px 7px 7px 50px}
.step::before{content:"";position:absolute;left:16px;top:14px;width:18px;height:18px;border-radius:4px;background:linear-gradient(135deg,#f7c948,#e85d5d)}
.step b{display:block;font-size:6.6px;color:var(--blue);text-transform:uppercase;margin-bottom:3px}
.step p{font-size:5.2px;line-height:1.9;color:var(--muted)}
.step--on{border-left:2px solid var(--blue)}
.proc-title{left:244px;top:1756px;font-size:15px}
.proc-sub{left:244px;top:1782px;font-size:7.4px;line-height:1.8;font-weight:500;color:var(--ink)}
.proc-text{left:244px;top:1812px;width:210px}
.proc-btn{left:244px;top:1895px}

/* clients */
.cl-title{left:0;width:515px;top:2031px;text-align:center;font-size:15px}
.cl-text{left:100px;width:315px;top:2054px;text-align:center}
.logos{left:74px;top:2092px;width:370px;display:grid;grid-template-columns:repeat(5,70px);gap:6px}
.logos span{height:40px;border:1px solid var(--line);display:flex;align-items:center;justify-content:center;font-size:7.6px;font-weight:500;color:var(--navy)}

/* footer */
.foot-shape{left:0;top:2200px}
.f-h{font-size:7.4px;color:var(--ink)}
.f-h::after{content:"";display:block;width:16px;height:1.5px;background:var(--blue);margin-top:4px}
.f-list{font-size:4.6px;line-height:2.2;color:var(--muted)}
.news-title{left:284px;top:2260px;font-size:15px;color:#fff}
.news-text{left:284px;top:2283px;font-size:4.8px;line-height:2.1;color:#fff}
.news-form{left:284px;top:2314px;width:164px;height:20px;background:#fff;border-radius:10px;font-size:4.6px;color:#999;padding:7px 14px}
.news-form b{position:absolute;right:0;top:0;height:20px;width:54px;background:var(--red);color:#fff;border-radius:10px;text-align:center;line-height:20px;font-size:5px}
.copy{left:310px;top:2354px;font-size:4.4px;color:#fff}
</style>
</head>
<body>

<!-- Concept A -->
<main class="page page--a">
  <div class="abs phone"><svg viewBox="0 0 14 14"><circle cx="7" cy="7" r="6.3" fill="none" stroke="#2a62aa" stroke-width="1"/><path d="M4.6 3.8l1.4-.2.6 1.6-.8.6a4 4 0 0 0 2 2l.6-.8 1.6.6-.2 1.4c-3 .4-5.6-2.2-5.2-5.2z" fill="#2a62aa"/></svg>+1 555 014 2278</div>
  <div class="abs social"><span></span><span></span><span></span><span></span></div>
  <nav class="abs nav"><span>Home</span><span>About</span><span>Services</span><span>Videos</span><span>Our Creative Work</span><span>Testimonials</span><span>Clients</span></nav>

  <svg class="abs hero-shape" width="515" height="260" viewBox="0 0 515 260"><path d="M170 40 C260 30 400 20 515 10 L515 251 C440 240 330 200 240 170 Z" fill="#2a62aa"/></svg>
  <div class="abs slider-dot" style="top:146px">‹</div>
  <div class="abs slider-dot" style="top:172px">›</div>
  <div class="abs mascot" role="img" aria-label="Mascot illustration: cartoon kid in a blue cap holding a paintbrush"></div>
  <div class="abs h wordmark">Copper Field</div>
  <h1 class="abs h hero-title">Copper Field<br>A Creative Collective</h1>
  <p class="abs hero-text">We are passionate about creating with you,<br>not just for you.</p>
  <span class="btn hero-btn">Connect with us</span>

  <svg class="abs about-shape" width="515" height="200" viewBox="0 0 515 200"><path d="M0 30 C30 8 70 0 100 10 C140 25 190 60 250 70 L250 170 C170 168 80 175 0 190 Z" fill="#2a62aa"/><path d="M0 192 C80 176 170 170 260 172 L260 180 C170 180 80 186 0 200 Z" fill="#e8ebf0"/></svg>
  <div class="abs laptop" role="img" aria-label="Illustration: presenter beside charts on a laptop screen"></div>
  <div class="abs laptop-base"></div>
  <h2 class="abs h about-title">About us</h2>
  <p class="abs body-txt about-text">Copper Field is a creative collective. We are built on what's great about the shared economy. With access to thousands of content creators, designers, technicians, writers, strategists and other creatives around the world, we are built differently than a traditional "brick and mortar" Marketing Agency.</p>
  <span class="btn about-btn">Read more</span>

  <h2 class="abs h svc-title">Copper Field Services</h2>
  <p class="abs body-txt svc-text">Lorem ipsum dolor sit amet, consectetur adipiscing elit, sed do eiusmod tempor incididunt ut labore et dolore magna aliqua uta enim minim veniam, quis nostrud exercitation ullamco laboris nisiut aliquip.</p>
  <svg class="abs svc-links" width="515" height="200" viewBox="0 0 515 200"><path d="M175 45 C230 10 290 10 335 45 M130 165 C140 120 150 80 175 45 M335 45 C370 80 390 120 400 165" fill="none" stroke="#e1e5ec" stroke-width="1"/></svg>
  <div class="abs svc svc--on" style="left:129px;top:576px"><span class="svc-fig" role="img" aria-label="Figure with rocket"></span><b>Strategy</b><i>Lorem ipsum dolor sit, consect adipiscing.</i></div>
  <div class="abs svc" style="left:289px;top:576px"><span class="svc-fig" role="img" aria-label="Figure with laptop"></span><b>Content</b><i>Lorem ipsum dolor sit, consect adipiscing.</i></div>
  <div class="abs svc" style="left:68px;top:697px"><span class="svc-fig" role="img" aria-label="Figure with lightbulb"></span><b>Discovery</b><i>Lorem ipsum dolor sit, consect adipiscing.</i></div>
  <div class="abs svc" style="left:355px;top:697px"><span class="svc-fig" role="img" aria-label="Figure beside large lightbulb"></span><b>Coaching</b><i>Lorem ipsum dolor sit, consect adipiscing.</i></div>
  <div class="abs mascot-sm" role="img" aria-label="Mascot illustration"></div>
  <div class="abs h wordmark-sm">Copper Field</div>

  <svg class="abs video-band" width="515" height="305" viewBox="0 0 515 305"><path d="M0 35 C170 -8 345 -8 515 35 L515 305 L0 305 Z" fill="#2a62aa"/></svg>
  <h2 class="abs h video-title">Our videos</h2>
  <div class="abs video" role="img" aria-label="Video still: team working at a desk with a laptop"><span class="abs play"></span></div>
  <span class="abs arrow" style="left:38px">‹</span><span class="abs arrow" style="left:466px">›</span>

  <h2 class="abs h work-title">Our creative work</h2>
  <div class="abs" style="left:68px;top:1228px;width:382px;height:215px">
    <div class="abs work" style="left:0;top:0" role="img" aria-label="Team planning around a table"><span>Lorem ipsum dolor</span></div>
    <div class="abs work" style="left:130px;top:0" role="img" aria-label="Colleagues reviewing a screen"><span>Lorem ipsums</span></div>
    <div class="abs work" style="left:260px;top:0" role="img" aria-label="Hands with tablet and icons"><span>Lorem ipsum dolor sitas</span></div>
    <div class="abs work" style="left:0;top:112px" role="img" aria-label="Businessman with tablet"><span>Lorem ipsums</span></div>
    <div class="abs work" style="left:130px;top:112px" role="img" aria-label="Hands on a touchscreen"><span>Lorem ipsum dolor sitas</span></div>
    <div class="abs work" style="left:260px;top:112px" role="img" aria-label="Charts on a monitor"><span>Lorem ipsum dolor</span></div>
  </div>
  <span class="btn work-btn">View more work</span>

  <svg class="abs testi-bg" width="515" height="240" viewBox="0 0 515 240"><path d="M0 60 C150 20 330 0 515 30 L515 240 L0 240 Z" fill="#f4f5f8"/></svg>
  <h2 class="abs h testi-title">Testimonials</h2>
  <span class="abs t-arrow" style="left:54px">‹</span><span class="abs t-arrow" style="left:457px">›</span>
  <div class="abs card" style="left:70px;top:1585px"><div class="who"><i></i>Marla Quinlan,<br>Harbor Stage</div><p>Copper Field is a driving force in our work and we look forward to partnering again soon.</p></div>
  <div class="abs card" style="left:202px;top:1585px"><div class="who"><i></i>Harbor Stage at the Linden<br>Center for Theatre</div><p>Through planning and filming, the team was very responsive to our input and needs.</p></div>
  <div class="abs card" style="left:334px;top:1585px"><div class="who"><i></i>Willow Dance<br>Studio</div><p>Copper Field helped us focus, shape our story and bring the whole company together.</p></div>

  <div class="abs step step--on" style="top:1712px"><b>Discovery</b><p>A facilitated Discovery conversation helps us to understand more about you, your mission, your aesthetic, your passion points and your narrative.</p></div>
  <div class="abs step" style="top:1798px"><b>Strategy</b><p>Let's face it, you can have the coolest car in the neighborhood but if it's hidden in the garage or the gas tank is empty, no one is going to know.</p></div>
  <div class="abs step" style="top:1877px"><b>Creative</b><p>Copper Field delivers imaginative, innovative, relatable content to clients looking to bring the "why" about their work into their messaging.</p></div>
  <h2 class="abs h proc-title">» Discovery</h2>
  <p class="abs proc-sub">We are passionate about creating with you,<br>not just for you.</p>
  <p class="abs body-txt proc-text">A facilitated Discovery conversation helps us to understand more about you, your mission, your aesthetic, your passion points and your narrative. In Discovery we look for your "why", find what moves you and shape ideas together about content and strategies that will propel your mission forward.</p>
  <span class="btn proc-btn">View next</span>

  <h2 class="abs h cl-title">Our clients</h2>
  <p class="abs body-txt cl-text">Lorem ipsum dolor sit amet, consectetur adipiscing elit, sed do eiusmod tempor incididunt ut labore et dolore magna aliqua uta enim minim veniam, quis nostrud exercitation ullamco laboris nisiut aliquip.</p>
  <div class="abs logos"><span>Ashford Valley</span><span>Millworks</span><span>Tall Tale</span><span>Brisk</span><span>Tetra</span><span>Firmhouse</span><span>Fine Flair</span><span>Sprout Lab</span><span>Paylane</span><span>Fernhall</span></div>

  <svg class="abs foot-shape" width="515" height="173" viewBox="0 0 515 173"><path d="M200 173 C250 110 280 30 350 22 C420 14 470 25 515 40 L515 173 Z" fill="#2a62aa"/></svg>
  <div class="abs" style="left:67px;top:2259px"><div class="h f-h">Contact us</div><div class="f-list" style="margin-top:6px">Email address<br>hello@copperfieldagency.com<br>Call us<br>+1 555 014 2278</div></div>
  <div class="abs" style="left:160px;top:2259px"><div class="h f-h">Links</div><div class="f-list" style="margin-top:6px">Home<br>Clients<br>About<br>Services<br>Testimonials<br>Creative Work<br>Contact</div></div>
  <h2 class="abs h news-title">Newsletter</h2>
  <p class="abs news-text">Lorem ipsum dolor sit amet, consectetur adipiscing elit,<br>sed do eiusmod tempor incididunt ut</p>
  <div class="abs news-form">Enter Your Email Address<b>SIGN UP</b></div>
  <p class="abs copy">© Copyrights 2019. Copper Field Agency. All Rights Reserved</p>
</main>

<!-- Concept B -->
<main class="page page--b">
  <div class="abs phone"><svg viewBox="0 0 14 14"><circle cx="7" cy="7" r="6.3" fill="none" stroke="#2a62aa" stroke-width="1"/><path d="M4.6 3.8l1.4-.2.6 1.6-.8.6a4 4 0 0 0 2 2l.6-.8 1.6.6-.2 1.4c-3 .4-5.6-2.2-5.2-5.2z" fill="#2a62aa"/></svg>+1 555 014 2278</div>
  <div class="abs social"><span></span><span></span><span></span><span></span></div>
  <nav class="abs nav"><span>Home</span><span>About</span><span>Services</span><span>Videos</span><span>Our Creative Work</span><span>Testimonials</span><span>Clients</span></nav>

  <svg class="abs hero-shape" width="515" height="260" viewBox="0 0 515 260"><path d="M194 40 C260 28 400 16 460 12 Q470 12 470 22 L470 175 Q470 186 460 186 L194 186 Z" fill="#2a62aa"/></svg>
  <div class="abs slider-dot" style="top:146px">‹</div>
  <div class="abs slider-dot" style="top:172px">›</div>
  <div class="abs mascot" role="img" aria-label="Mascot illustration: cartoon kid in a blue cap holding a paintbrush"></div>
  <div class="abs h wordmark">Copper Field</div>
  <h1 class="abs h hero-title" style="top:116px">Copper Field<br>A Creative Collective</h1>
  <p class="abs hero-text" style="top:166px">We are passionate about creating with you,<br>not just for you.</p>
  <span class="btn hero-btn" style="top:202px">Connect with us</span>

  <svg class="abs about-shape" width="515" height="200" viewBox="0 0 515 200"><path d="M0 36 C30 14 70 6 100 16 C140 31 190 66 250 76 L250 176 C170 174 80 181 0 196 Z" fill="#2a62aa"/></svg>
  <div class="abs laptop" style="top:346px" role="img" aria-label="Illustration: presenter beside charts on a laptop screen"></div>
  <div class="abs laptop-base" style="top:448px"></div>
  <h2 class="abs h about-title" style="top:354px">About us</h2>
  <p class="abs body-txt about-text" style="top:377px">Copper Field is a creative collective. We are built on what's great about the shared economy. With access to thousands of content creators, designers, technicians, writers, strategists and other creatives around the world, we are built differently than a traditional "brick and mortar" Marketing Agency.</p>
  <span class="btn about-btn" style="top:451px">Read more</span>

  <h2 class="abs h svc-title" style="top:528px">Copper Field Services</h2>
  <p class="abs body-txt svc-text" style="top:552px">Lorem ipsum dolor sit amet, consectetur adipiscing elit, sed do eiusmod tempor incididunt ut labore et dolore magna aliqua uta enim minim veniam, quis nostrud exercitation ullamco laboris nisiut aliquip.</p>
  <svg class="abs svc-links" style="top:588px" width="515" height="200" viewBox="0 0 515 200"><path d="M175 45 C230 10 290 10 335 45 M130 165 C140 120 150 80 175 45 M335 45 C370 80 390 120 400 165" fill="none" stroke="#e1e5ec" stroke-width="1"/></svg>
  <div class="abs svc svc--on" style="left:129px;top:584px"><span class="svc-fig" role="img" aria-label="Figure with rocket"></span><b>Strategy</b><i>Lorem ipsum dolor sit, consect adipiscing.</i></div>
  <div class="abs svc" style="left:289px;top:584px"><span class="svc-fig" role="img" aria-label="Figure with laptop"></span><b>Content</b><i>Lorem ipsum dolor sit, consect adipiscing.</i></div>
  <div class="abs svc" style="left:68px;top:705px"><span class="svc-fig" role="img" aria-label="Figure with lightbulb"></span><b>Discovery</b><i>Lorem ipsum dolor sit, consect adipiscing.</i></div>
  <div class="abs svc" style="left:355px;top:705px"><span class="svc-fig" role="img" aria-label="Figure beside large lightbulb"></span><b>Coaching</b><i>Lorem ipsum dolor sit, consect adipiscing.</i></div>
  <div class="abs mascot-sm" style="top:676px" role="img" aria-label="Mascot illustration"></div>
  <div class="abs h wordmark-sm" style="top:800px">Copper Field</div>

  <svg class="abs video-band" style="top:864px" width="515" height="305" viewBox="0 0 515 305"><path d="M0 35 C170 -8 345 -8 515 35 L515 305 L0 305 Z" fill="#2a62aa"/></svg>
  <h2 class="abs h video-title" style="top:904px">Our videos</h2>
  <div class="abs video" style="top:935px" role="img" aria-label="Video still: team working at a desk with a laptop"><span class="abs play"></span></div>
  <span class="abs arrow" style="left:38px;top:1014px">‹</span><span class="abs arrow" style="left:466px;top:1014px">›</span>

  <h2 class="abs h work-title">Our creative work</h2>
  <div class="abs" style="left:68px;top:1228px;width:382px;height:215px">
    <div class="abs work" style="left:0;top:0" role="img" aria-label="Team planning around a table"><span>Lorem ipsum dolor</span></div>
    <div class="abs work" style="left:130px;top:0" role="img" aria-label="Colleagues reviewing a screen"><span>Lorem ipsums</span></div>
    <div class="abs work" style="left:260px;top:0" role="img" aria-label="Hands with tablet and icons"><span>Lorem ipsum dolor sitas</span></div>
    <div class="abs work" style="left:0;top:112px" role="img" aria-label="Businessman with tablet"><span>Lorem ipsums</span></div>
    <div class="abs work" style="left:130px;top:112px" role="img" aria-label="Hands on a touchscreen"><span>Lorem ipsum dolor sitas</span></div>
    <div class="abs work" style="left:260px;top:112px" role="img" aria-label="Charts on a monitor"><span>Lorem ipsum dolor</span></div>
  </div>
  <span class="btn work-btn">View more work</span>

  <svg class="abs testi-bg" width="515" height="240" viewBox="0 0 515 240"><path d="M0 60 C150 20 330 0 515 30 L515 240 L0 240 Z" fill="#f4f5f8"/></svg>
  <h2 class="abs h testi-title">Testimonials</h2>
  <span class="abs t-arrow" style="left:54px">‹</span><span class="abs t-arrow" style="left:457px">›</span>
  <div class="abs card" style="left:70px;top:1585px"><div class="who"><i></i>Marla Quinlan,<br>Harbor Stage</div><p>Copper Field is a driving force in our work and we look forward to partnering again soon.</p></div>
  <div class="abs card" style="left:202px;top:1585px"><div class="who"><i></i>Harbor Stage at the Linden<br>Center for Theatre</div><p>Through planning and filming, the team was very responsive to our input and needs.</p></div>
  <div class="abs card" style="left:334px;top:1585px"><div class="who"><i></i>Willow Dance<br>Studio</div><p>Copper Field helped us focus, shape our story and bring the whole company together.</p></div>

  <div class="abs step step--on" style="top:1712px"><b>Discovery</b><p>A facilitated Discovery conversation helps us to understand more about you, your mission, your aesthetic, your passion points and your narrative.</p></div>
  <div class="abs step" style="top:1798px"><b>Strategy</b><p>Let's face it, you can have the coolest car in the neighborhood but if it's hidden in the garage or the gas tank is empty, no one is going to know.</p></div>
  <div class="abs step" style="top:1877px"><b>Creative</b><p>Copper Field delivers imaginative, innovative, relatable content to clients looking to bring the "why" about their work into their messaging.</p></div>
  <h2 class="abs h proc-title">» Discovery</h2>
  <p class="abs proc-sub">We are passionate about creating with you,<br>not just for you.</p>
  <p class="abs body-txt proc-text">A facilitated Discovery conversation helps us to understand more about you, your mission, your aesthetic, your passion points and your narrative. In Discovery we look for your "why", find what moves you and shape ideas together about content and strategies that will propel your mission forward.</p>
  <span class="btn proc-btn">View next</span>

  <h2 class="abs h cl-title">Our clients</h2>
  <p class="abs body-txt cl-text">Lorem ipsum dolor sit amet, consectetur adipiscing elit, sed do eiusmod tempor incididunt ut labore et dolore magna aliqua uta enim minim veniam, quis nostrud exercitation ullamco laboris nisiut aliquip.</p>
  <div class="abs logos"><span>Ashford Valley</span><span>Millworks</span><span>Tall Tale</span><span>Brisk</span><span>Tetra</span><span>Firmhouse</span><span>Fine Flair</span><span>Sprout Lab</span><span>Paylane</span><span>Fernhall</span></div>

  <svg class="abs foot-shape" width="515" height="173" viewBox="0 0 515 173"><path d="M200 173 C250 110 280 30 350 22 C420 14 470 25 515 40 L515 173 Z" fill="#2a62aa"/></svg>
  <div class="abs" style="left:67px;top:2259px"><div class="h f-h">Contact us</div><div class="f-list" style="margin-top:6px">Email address<br>hello@copperfieldagency.com<br>Call us<br>+1 555 014 2278</div></div>
  <div class="abs" style="left:160px;top:2259px"><div class="h f-h">Links</div><div class="f-list" style="margin-top:6px">Home<br>Clients<br>About<br>Services<br>Testimonials<br>Creative Work<br>Contact</div></div>
  <h2 class="abs h news-title">Newsletter</h2>
  <p class="abs news-text">Lorem ipsum dolor sit amet, consectetur adipiscing elit,<br>sed do eiusmod tempor incididunt ut</p>
  <div class="abs news-form">Enter Your Email Address<b>SIGN UP</b></div>
  <p class="abs copy">© Copyrights 2019. Copper Field Agency. All Rights Reserved</p>
</main>

</body>
</html>
```